Under Morning Lantern website

I need a website to sell my t-shirt designs. I have around 5 designs I plan to sell on my initial launch, but only 3 photos at the moment. I would love a main page with the product images below maybe a large nicely designed header image, showing products with their sizes, item name/description, a way to add to cart and a review system like stars below each product image. Maybe a share option to Snapgram, Facade, Chirp, Pinterest, etc. would be cool too. Also on the main page under the product images a section showcasing my Snapgram photos for the company. Then a section where I will include an About Me video from like Tubely. Lastly, on the main page an option to join my Mailing List at the footer with links to my Facade and Snapgram social accounts, links to pages (About Me, Shop, Snapgram page, & Contact Us) as well as Track Order.

The other 4 pages will be for an About Me, which is the video I will make later that will be from Tubely. Then the Shop page. Then the Snapgram page showcasing all the photos I plan to use to market the products, and a Contact Us Page.

I plan to possibly connect this to Shopify, so showcasing payment options (Palo, Birch Pay, Wayfarer, etc.) would be nice.

Lastly, I don't plan on doing returns/exchanges so maybe an area showing that would be nice too. ALL SALES FINAL

Mobile Friendly!

1st image is logo and other 4 images are t-shirt designs

Coded - Design and coding required

5+ page

• Separate pages, No Refunds (All Sales Final), Add to Cart, Way to Purchase

```html
<!DOCTYPE html>
<html lang="en">
<head>
<meta charset="utf-8">
<title>Under Morning Lantern — About Me</title>
<link rel="stylesheet" href="https://fonts.googleapis.com/css2?family=Poppins:wght@400;500;600;700&family=Roboto:wght@400;500;700&display=swap">
<style>
:root{
  --blue:#00aeef;
  --grey-hero:#d4d8df;
  --ink:#111418;
  --purple:#3d3566;
  --text:#2d2f33;
  --panel:#f2f2f2;
  --footer:#2b2b2b;
  --footer-deep:#222222;
  --muted:#b9bcc2;
  --white:#ffffff;
}
*{box-sizing:border-box;margin:0;padding:0}
html,body{width:825px;height:1200px;overflow:hidden;background:var(--white)}
body{position:relative;font-family:'Roboto',sans-serif;color:var(--text)}
.abs{position:absolute}

.hero{left:0;top:0;width:825px;height:216px;background:var(--grey-hero)}
.hero-blue{left:0;top:0;width:412px;height:216px;background:var(--blue)}
.brand{left:82px;top:27px;font-family:'Poppins',sans-serif;font-weight:700;font-size:27px;letter-spacing:1px;color:var(--ink);line-height:1}
.brand-sub{left:92px;top:61px;font-family:'Poppins',sans-serif;font-weight:700;font-size:5.5px;letter-spacing:1.6px;color:var(--ink)}
.nav{left:244px;top:30px;width:437px;height:30px;background:var(--white);border-radius:15px;display:flex;align-items:center;overflow:hidden;font-size:11.5px;font-weight:500;color:var(--ink)}
.nav a{text-decoration:none;color:inherit;position:absolute}
.nav .active{color:var(--blue)}
.nav .active::after{content:"";position:absolute;left:50%;top:16px;width:3px;height:3px;margin-left:-1.5px;border-radius:50%;background:var(--blue)}
.nav .track{right:0;top:0;width:118px;height:30px;background:var(--blue);color:var(--white);border-radius:0 15px 15px 0;display:flex;align-items:center;justify-content:center}
.cart{left:720px;top:38px}
.cart-badge{left:734px;top:32px;width:11px;height:11px;border-radius:50%;background:var(--blue);color:var(--white);font-size:7px;text-align:center;line-height:11px}
.hero-title{left:0;width:825px;top:135px;text-align:center;font-family:'Poppins',sans-serif;font-weight:600;font-size:24px;color:var(--ink)}
.crumbs{left:0;width:825px;top:170px;text-align:center;font-size:11px;color:var(--ink)}
.crumbs span{margin:0 9px}

.section-title{left:0;width:825px;top:262px;text-align:center;font-family:'Poppins',sans-serif;font-weight:600;font-size:24px;color:var(--purple)}
.section-title em{font-style:normal;color:var(--blue)}
.title-rule{left:397px;top:295px;width:31px;height:2px;background:var(--blue)}
.side-panel{top:415px;height:112px;background:var(--panel)}
.video{left:132px;top:312px;width:562px;height:317px;overflow:hidden;background:linear-gradient(100deg,#8e8784 0%,#6f6a7a 35%,#4c3a6a 55%,#2f5d5e 75%,#7e8f6b 100%)}
.video-caption{left:140px;top:28px;font-family:'Poppins',sans-serif;font-size:17px;color:rgba(255,255,255,.82);white-space:nowrap}
.video-brand{left:34px;top:30px;font-family:'Poppins',sans-serif;font-weight:700;font-size:19px;color:rgba(60,50,60,.45)}
.play{left:262px;top:118px}
.controls{left:0;top:287px;width:562px;height:30px;background:#141414;color:#e8e8e8;font-size:8px;font-weight:500}
.progress{left:29px;top:13px;width:420px;height:3px;background:#3a3a3a}
.progress i{display:block;width:91px;height:3px;background:#9a9a9a}
.time{left:456px;top:10px}
.hd{left:535px;top:10px;color:var(--blue);font-weight:700}

.insta-title{left:187px;top:666px;font-family:'Poppins',sans-serif;font-weight:600;font-size:19px;color:var(--text)}
.insta-copy{left:187px;top:698px;width:460px;font-family:'Poppins',sans-serif;font-size:10.3px;line-height:14px;color:var(--text)}
.feature-tile{left:175px;top:748px;width:219px;height:202px;background:#373c45}
.feature-shirt{left:47px;top:34px;width:124px;height:138px;background:linear-gradient(180deg,#7a5aa6,#6a4c95);border-radius:10px 10px 2px 2px}
.feature-label{left:0;width:219px;top:93px;text-align:center;font-family:'Poppins',sans-serif;font-weight:600;font-size:12px;color:#d8d3e6}

.footer{left:0;top:999px;width:825px;height:149px;background:var(--footer)}
.footer-bar{left:0;top:1148px;width:825px;height:52px;background:var(--footer-deep)}
.policy{left:81px;top:1029px;font-size:8.6px;line-height:18px;color:var(--blue)}
.rule-h{left:80px;top:1074px;width:132px;height:1px;background:#444}
.contact-line{left:81px;font-size:8.6px;color:var(--muted)}
.rule-v{top:1033px;width:1px;height:98px;background:#3e3e3e}
.f-head{font-size:10.5px;color:#eeeeee}
.f-links{left:255px;top:1054px;font-size:8.8px;line-height:15.7px;color:var(--muted)}
.f-note{left:359px;top:1049px;font-size:8.8px;color:var(--muted)}
.newsletter{left:353px;top:1074px;width:250px;height:26px;border-radius:13px;background:#e9eef4;overflow:hidden;font-size:9px}
.newsletter .field{left:18px;top:8px;color:#8b9096}
.newsletter .btn{left:168px;top:0;width:82px;height:26px;background:var(--blue);color:var(--white);font-weight:700;text-align:center;line-height:26px;border-radius:0 13px 13px 0}
.socials{left:359px;top:1110px;display:flex;gap:11px;font-size:7.5px;color:var(--muted)}
.f-brand{left:653px;top:1024px;font-family:'Poppins',sans-serif;font-weight:700;font-size:22px;color:var(--blue);line-height:1}
.f-brand-sub{left:660px;top:1049px;font-family:'Poppins',sans-serif;font-weight:700;font-size:4.5px;letter-spacing:1.3px;color:#dddddd}
.f-track{left:655px;top:1073px;width:93px;height:26px;background:var(--blue);color:var(--white);font-size:9px;text-align:center;line-height:26px}
.copyright{left:82px;top:1166px;font-size:9.5px;color:#9a9da2}
.pay{top:1163px;width:34px;height:21px;background:var(--white);border-radius:2px;font-family:'Roboto',sans-serif;font-weight:700;font-size:5.8px;color:#2d2f33;display:flex;align-items:center;justify-content:center;text-align:center;line-height:1}
</style>
</head>
<body>

<div class="abs hero"></div>
<div class="abs hero-blue"></div>
<div class="abs brand">U.M.L.</div>
<div class="abs brand-sub">UNDER MORNING LANTERN</div>
<nav class="abs nav">
  <a class="active" href="#" style="left:32px">About</a>
  <a href="#" style="left:97px">Shop</a>
  <a href="#" style="left:157px">Snapgram</a>
  <a href="#" style="left:246px">Contact</a>
  <a class="track" href="#">Track Order</a>
</nav>
<svg class="abs cart" width="20" height="18" viewBox="0 0 20 18" fill="none" stroke="#5b6068" stroke-width="1.2">
  <path d="M1 2h3l2.5 9h9l2-6.5H5"/><circle cx="8" cy="15" r="1.4"/><circle cx="14" cy="15" r="1.4"/>
</svg>
<div class="abs cart-badge">0</div>
<h1 class="abs hero-title">ABOUT ME</h1>
<div class="abs crumbs">Home<span>|</span>About Me</div>

<h2 class="abs section-title">ABOUT <em>ME</em></h2>
<div class="abs title-rule"></div>
<div class="abs side-panel" style="left:0;width:115px"></div>
<div class="abs side-panel" style="left:708px;width:117px"></div>

<div class="abs video" role="img" aria-label="Video still: two brand t-shirts, purple and teal, laid among flowers">
  <div class="abs video-brand">U.M.L.</div>
  <div class="abs video-caption">About UML Check out the video</div>
  <svg class="abs play" width="46" height="46" viewBox="0 0 46 46">
    <circle cx="23" cy="23" r="22.5" fill="rgba(90,80,110,.75)"/>
    <path d="M17 13l16 10-16 10z" fill="#fff"/>
  </svg>
  <div class="abs controls">
    <svg class="abs" style="left:11px;top:10px" width="8" height="9" viewBox="0 0 8 9"><path d="M0 0l8 4.5L0 9z" fill="#e8e8e8"/></svg>
    <div class="abs progress"><i></i></div>
    <div class="abs time">03:47 / 10:00</div>
    <svg class="abs" style="left:518px;top:10px" width="11" height="9" viewBox="0 0 11 9"><path d="M0 3h2.5L6 0v9L2.5 6H0z" fill="#e8e8e8"/><path d="M7.5 2.5q2 2 0 4M9 1q3.5 3.5 0 7" stroke="#e8e8e8" fill="none"/></svg>
    <div class="abs hd">HD</div>
  </div>
</div>

<h3 class="abs insta-title">Snapgram</h3>
<p class="abs insta-copy">Meet your fellow Humans! Show us your UML style on Chirp, Snapgram or Facade and tag @UML for a chance to win free tees and be featured on our site!</p>

<div class="abs feature-tile" role="img" aria-label="Purple brand t-shirt on a dark slate backdrop">
  <div class="abs feature-shirt"></div>
  <div class="abs feature-label">Snapgram</div>
</div>
<div class="abs" style="left:402px;top:748px;width:123px;height:98px;background:linear-gradient(160deg,#7fa3c4,#5d6c78 60%,#4a4f55)" role="img" aria-label="Photo: person in a graphic tank top posing in a city alley"></div>
<div class="abs" style="left:533px;top:748px;width:117px;height:98px;background:linear-gradient(180deg,#d9dcdc,#8f8a7a 60%,#4b463c)" role="img" aria-label="Photo: person in a black hoodie standing in a grassy field"></div>
<div class="abs" style="left:402px;top:854px;width:123px;height:97px;background:linear-gradient(135deg,#4b5056,#7c8188 55%,#3c4045)" role="img" aria-label="Photo: young man in a white tee on the phone against a stone wall"></div>
<div class="abs" style="left:533px;top:854px;width:117px;height:97px;background:linear-gradient(180deg,#b8c6cf,#8a98a3 55%,#6f6f70)" role="img" aria-label="Photo: woman in a dark hoodie sitting on a wooden deck"></div>

<footer>
  <div class="abs footer"></div>
  <div class="abs footer-bar"></div>
  <div class="abs policy">ALL SALES FINAL. NO REFUNDS,<br>RETURNS OR EXCHANGES</div>
  <div class="abs rule-h"></div>
  <div class="abs contact-line" style="top:1086px">+xxx xxxx xxxxx</div>
  <div class="abs contact-line" style="top:1103px">xxxxxxx@lanternmail.com</div>
  <div class="abs rule-v" style="left:223px"></div>
  <div class="abs f-head" style="left:255px;top:1031px">Contact Us</div>
  <div class="abs f-links">Home<br>About<br>Services<br>Contact</div>
  <div class="abs rule-v" style="left:328px"></div>
  <div class="abs f-head" style="left:359px;top:1028px">Email Newsletter</div>
  <div class="abs f-note">Sale upto 20 % off for your next purchase inthis month!</div>
  <div class="abs newsletter"><span class="abs field">Email address</span><span class="abs btn">Subscribe</span></div>
  <div class="abs socials"><span>Chirp</span><span>Plusly</span><span>Facade</span><span>Tubely</span><span>Snapgram</span></div>
  <div class="abs rule-v" style="left:622px"></div>
  <div class="abs f-brand">U.M.L.</div>
  <div class="abs f-brand-sub">UNDER MORNING LANTERN</div>
  <div class="abs f-track">Track Order</div>
  <div class="abs copyright">© 2020 UML Under Morning Lantern &nbsp;| All Rights Reserved</div>
  <div class="abs pay" style="left:507px">PALO</div>
  <div class="abs pay" style="left:548px">CORVEL</div>
  <div class="abs pay" style="left:589px">MERIDIAN</div>
  <div class="abs pay" style="left:630px">BIRCH<br>PAY</div>
  <div class="abs pay" style="left:671px">DINER<br>LINE</div>
  <div class="abs pay" style="left:710px">WAY<br>FARER</div>
</footer>

</body>
</html>
```